Custom Software Solutions

web design for a small custom programming company in Brisbane Australia. Specialize in business finance solutions, MS Office automation and programming and data analysis. The design should portray professionalism and honesty. Main applications deal with financial accounting reporting and analysis. Would like to see colors blue and purple used (but sparsely). added file is company logo. Trading name is TR Solutions, while the official company name is TR Solutions (QLD) Pty Ltd.

Target Market(s)

current clients for support
marketing tool for prospective clients

Industry/Entity Type

Business

Number of Pages Required

5+ page

Font styles to use
Sans Serif

Colors
0555a3
a54599
ffffff

Requirements
Must have
• introduction
• blog for news and tips
• previous and current clients/projects page
• contact us page with email submission form
Should not have
• social media links

```html
<!DOCTYPE html>
<html lang="en">
<head>
<meta charset="utf-8">
<title>TR Solutions</title>
<link href="https://fonts.googleapis.com/css2?family=Open+Sans:wght@400;600;700&family=Arimo:wght@400&family=Tinos:wght@400&display=swap" rel="stylesheet">
<style>
:root{
  --blue:#0555a3;
  --purple:#a54599;
  --white:#ffffff;
  --ink:#333333;
  --muted:#888888;
  --topbar:#f5f5f5;
  --band:#f1f1f1;
  --rule:#e2e2e2;
  --dark:#3a3a3a;
}
*{margin:0;padding:0;box-sizing:border-box}
html,body{width:920px;height:1200px;overflow:hidden;background:var(--white)}
body{font-family:"Arimo",Arial,sans-serif;color:var(--ink);position:relative}
.abs{position:absolute}
.topbar{left:0;top:0;width:920px;height:34px;background:var(--topbar);border-top:3px solid var(--blue);border-bottom:1px solid var(--rule);font-size:8px;color:#666}
.topbar .item{position:absolute;top:0;height:31px;line-height:31px;padding:0 10px;border-right:1px solid var(--rule);display:flex;align-items:center;gap:4px}
.topbar .search{position:absolute;left:792px;top:0;width:30px;height:31px;border-left:1px solid var(--rule);display:flex;align-items:center;justify-content:center}
.header{left:0;top:34px;width:920px;height:72px}
.brand{position:absolute;left:100px;top:20px;display:flex;align-items:center;gap:7px;font-family:"Open Sans",sans-serif;font-size:17px;font-weight:600;color:var(--blue);letter-spacing:1px}
.brand .dot{width:22px;height:22px;border-radius:50%;background:var(--blue)}
.nav{position:absolute;top:0;height:72px;line-height:72px;font-family:"Open Sans",sans-serif;font-size:10.5px;color:#666}
.nav.active{color:var(--blue);font-weight:600}
.hero{left:0;top:106px;width:920px;height:354px;background:linear-gradient(180deg,#b9c6d3 0%,#cfd6dc 45%,#9aa1a8 80%,#7d8084 100%)}
.hero-box{position:absolute;left:107px;top:98px;width:396px;height:164px;background:rgba(210,215,222,.55);padding:12px 20px}
.hero-title{font-family:"Tinos",serif;font-size:45px;color:var(--blue);line-height:44px}
.hero-sub{font-family:"Arimo",sans-serif;font-size:13.5px;color:#333;margin-top:6px;margin-left:4px}
.hero-text{font-size:10px;line-height:21px;color:var(--white);margin-top:8px;margin-left:4px}
.arrow{position:absolute;top:317px;width:22px;height:20px;background:#2b2b2b;display:flex;align-items:center;justify-content:center}
.welcome-title{left:0;top:482px;width:920px;text-align:center;font-family:"Open Sans",sans-serif;font-weight:700;font-size:18px;color:var(--blue)}
.welcome-rule{left:430px;top:515px;width:60px;height:1px;background:var(--blue)}
.welcome-text{left:170px;top:532px;width:580px;text-align:center;font-size:8.8px;line-height:17px;color:var(--muted)}
.services{left:0;top:580px;width:920px;height:270px;background:var(--band)}
.service{position:absolute;top:0;width:170px;text-align:center}
.service .icon{width:77px;height:77px;margin:23px auto 0;border-radius:50%;background:radial-gradient(circle at 50% 40%,#ffffff 0%,#e6e6e6 70%,#d5d5d5 100%);border:3px solid #fff;box-shadow:0 1px 3px rgba(0,0,0,.25);display:flex;align-items:center;justify-content:center}
.service h3{font-family:"Open Sans",sans-serif;font-weight:400;font-size:9.5px;color:#333;margin-top:20px}
.service p{font-size:8.6px;line-height:16.5px;color:var(--muted);margin-top:9px}
.btn{display:inline-block;margin-top:14px;width:86px;height:30px;line-height:30px;background:var(--blue);color:var(--white);font-size:10.5px}
.section-title{font-family:"Open Sans",sans-serif;font-weight:700;font-size:13px;color:var(--blue)}
.project{position:absolute;top:902px;width:190px}
.project .photo{width:190px;height:127px;border:1px solid #ccc;padding:2px;background:#fff}
.project .photo div{width:100%;height:100%}
.project h4{font-family:"Arimo",sans-serif;font-weight:400;font-size:10.5px;color:var(--blue);margin-top:9px}
.project .date{font-size:8.6px;color:var(--purple);margin-top:5px}
.project p{font-size:8.6px;line-height:17px;color:var(--muted);margin-top:4px;width:185px}
.project p span{color:var(--purple)}
.news{position:absolute;left:519px;width:302px}
.news .date-box{position:absolute;left:3px;top:3px;width:26px;height:27px;background:var(--dark);color:var(--white);font-size:8.5px;text-align:center;line-height:11px;padding-top:3px}
.news h5{margin-left:38px;font-weight:400;font-size:9px;line-height:14px;color:#333;padding-top:1px}
.news p{margin-left:3px;margin-top:13px;font-size:8.5px;line-height:17px;color:var(--muted)}
.news-rule{left:519px;top:990px;width:302px;height:1px;background:var(--rule)}
.footer{left:0;top:1134px;width:920px;height:66px;background:var(--blue);color:var(--white);font-size:8.6px}
.footer .links{position:absolute;left:101px;top:28px;display:flex;gap:12px}
.footer .copy{position:absolute;left:605px;top:29px}
</style>
</head>
<body>

<div class="abs topbar">
  <div class="item" style="left:92px">
    <svg width="8" height="8" viewBox="0 0 10 10"><path d="M2 1l2 2-1 1.5c.8 1.3 1.5 2 2.5 2.5L7 6l2 2-1.5 1.5C4.5 9 1 5.5.5 2.5z" fill="#777"/></svg>
    Call Us : 61-4-05550123
  </div>
  <div class="item" style="left:209px">
    <svg width="8" height="8" viewBox="0 0 10 10"><circle cx="5" cy="3" r="2.3" fill="#777"/><path d="M1 10c0-3 2-4.5 4-4.5S9 7 9 10z" fill="#777"/></svg>
    Login
  </div>
  <div class="item" style="left:265px">
    <svg width="8" height="8" viewBox="0 0 10 10"><path d="M1 9l1-3 5-5 2 2-5 5z" fill="#777"/></svg>
    Register
  </div>
  <div class="search">
    <svg width="9" height="9" viewBox="0 0 10 10"><circle cx="4" cy="4" r="3" fill="none" stroke="#666" stroke-width="1.4"/><path d="M6.3 6.3L9 9" stroke="#666" stroke-width="1.5"/></svg>
  </div>
</div>

<div class="abs header">
  <div class="brand"><span class="dot"></span>TR Solutions</div>
  <div class="nav active" style="left:381px">HOME</div>
  <div class="nav" style="left:442px">ABOUT US</div>
  <div class="nav" style="left:522px">SERVICES</div>
  <div class="nav" style="left:597px">RECENTS BLOG</div>
  <div class="nav" style="left:699px">NEWS</div>
  <div class="nav" style="left:758px">CONTACT US</div>
</div>

<div class="abs hero" role="img" aria-label="City skyline under a cloudy sky with a businessman leaping with a briefcase">
  <div class="hero-box">
    <div class="hero-title">TR SOLUTION</div>
    <div class="hero-sub">NEQUE PORRO QUISQUAM EST QUI DOLOREM</div>
    <div class="hero-text">Sed ut perspiciatis unde omnis iste natus error sit voluptatem accusantium doloremque laudantium, totam rem aperiam, eaque ipsa quae ab illo inventore veritatis et quasi architecto beatae vitae dicta sunt explicabo.</div>
  </div>
  <div class="arrow" style="left:108px"><svg width="8" height="10" viewBox="0 0 8 10"><path d="M6 1L2 5l4 4" fill="none" stroke="#fff" stroke-width="1.6"/></svg></div>
  <div class="arrow" style="left:137px"><svg width="8" height="10" viewBox="0 0 8 10"><path d="M2 1l4 4-4 4" fill="none" stroke="#fff" stroke-width="1.6"/></svg></div>
</div>

<h1 class="abs welcome-title">WELCOME TO TR SOLUTIONS</h1>
<div class="abs welcome-rule"></div>
<p class="abs welcome-text">Sed ut perspiciatis unde omnis iste natus error sit voluptatem accusantium doloremque laudantium, totam rem aperiam, eaque ipsa quae ab illo inventore veritatis et quasi architecto beatae vitae dicta sunt explicabo.</p>

<div class="abs services">
  <div class="service" style="left:99px">
    <div class="icon"><svg width="34" height="30" viewBox="0 0 34 30"><rect x="2" y="2" width="30" height="20" rx="2" fill="none" stroke="#333" stroke-width="2.4"/><rect x="14" y="22" width="6" height="4" fill="#333"/><rect x="9" y="26" width="16" height="2.4" fill="#333"/><circle cx="10" cy="12" r="4" fill="#333"/><rect x="17" y="12" width="2.5" height="6" fill="#333"/><rect x="21" y="9" width="2.5" height="9" fill="#333"/><rect x="25" y="7" width="2.5" height="11" fill="#333"/></svg></div>
    <h3>BUSINESS FINANCE SOLUTIONS</h3>
    <p>Sed ut perspiciatis unde omnis iste natus error sit voluptatem accusantium dolor beatae&nbsp; dicta sunt explicabo.</p>
    <span class="btn">READ MORE</span>
  </div>
  <div class="service" style="left:282px">
    <div class="icon"><svg width="36" height="26" viewBox="0 0 36 26"><circle cx="9" cy="8" r="4.5" fill="#333"/><circle cx="27" cy="8" r="4.5" fill="#333"/><path d="M1 22c0-6 4-8 8-8s8 2 8 8z" fill="#333"/><path d="M19 22c0-6 4-8 8-8s8 2 8 8z" fill="#333"/><circle cx="18" cy="7" r="5.5" fill="#333" stroke="#e8e8e8" stroke-width="1.5"/><path d="M8 25c0-7 5-10 10-10s10 3 10 10z" fill="#333" stroke="#e8e8e8" stroke-width="1.5"/></svg></div>
    <h3>MS OFFICE AUTOMATION</h3>
    <p>Sed ut perspiciatis unde omnis iste natus error sit voluptatem accusantium dolor beatae&nbsp; dicta sunt explicabo.</p>
    <span class="btn">READ MORE</span>
  </div>
  <div class="service" style="left:465px">
    <div class="icon"><svg width="30" height="34" viewBox="0 0 30 34"><path d="M5 3h20v24a4 4 0 0 1-4 4H3" fill="none" stroke="#333" stroke-width="2.4"/><path d="M5 3v24a4 4 0 0 1-4 4" fill="none" stroke="#333" stroke-width="2.4"/><path d="M12 11l-3 4 3 4M18 11l3 4-3 4" fill="none" stroke="#333" stroke-width="2"/></svg></div>
    <h3>PROGRAMMING</h3>
    <p>Sed ut perspiciatis unde omnis iste natus error sit voluptatem accusantium dolor beatae&nbsp; dicta sunt explicabo.</p>
    <span class="btn">READ MORE</span>
  </div>
  <div class="service" style="left:648px">
    <div class="icon"><svg width="34" height="32" viewBox="0 0 34 32"><ellipse cx="13" cy="5" rx="11" ry="3.5" fill="#333"/><path d="M2 8c0 2 5 3.5 11 3.5S24 10 24 8v5c0 2-5 3.5-11 3.5S2 15 2 13zM2 16c0 2 5 3.5 11 3.5v5C7 24.5 2 23 2 21z" fill="#333"/><circle cx="24" cy="23" r="7" fill="none" stroke="#333" stroke-width="2.4"/><path d="M17 18l1 5 4-2" fill="#333"/></svg></div>
    <h3>DATA ANALYSIS</h3>
    <p>Sed ut perspiciatis unde omnis iste natus error sit voluptatem accusantium dolor beatae&nbsp; dicta sunt explicabo.</p>
    <span class="btn">READ MORE</span>
  </div>
</div>

<h2 class="abs section-title" style="left:101px;top:873px">RECENT PROJECTS</h2>
<div class="project" style="left:101px">
  <div class="photo"><div role="img" aria-label="Hand on a computer mouse with financial charts" style="background:linear-gradient(135deg,#2f6d86 0%,#7fb8cc 50%,#e6eef2 100%)"></div></div>
  <h4>NEQUE PORRO QUISQUAM</h4>
  <div class="date">22 Aug 2014</div>
  <p>Sed ut perspiciatis unde omnis iste natus error vitae dicta sunt explicabo. <span>READ MORE</span></p>
</div>
<div class="project" style="left:306px">
  <div class="photo"><div role="img" aria-label="Business team climbing a rising red growth arrow" style="background:linear-gradient(180deg,#dfe4ea 0%,#c5ccd4 60%,#9ea4aa 100%)"></div></div>
  <h4>NEQUE PORRO QUISQUAM</h4>
  <div class="date">22 Aug 2014</div>
  <p>Sed ut perspiciatis unde omnis iste natus error vitae dicta sunt explicabo. <span>READ MORE</span></p>
</div>

<h2 class="abs section-title" style="left:519px;top:873px">LATEST NEWS</h2>
<div class="news" style="top:902px">
  <div class="date-box">24<br>Jun</div>
  <h5>Neque porro quisquam est qui dolorem ipsum quia dolor sit amet, consectetur....</h5>
  <p>Sed ut perspiciatis unde omnis iste natus error sit&nbsp; accusantium doloremque error sit&nbsp; laudantium........</p>
</div>
<div class="abs news-rule"></div>
<div class="news" style="top:1004px">
  <div class="date-box">24<br>Jun</div>
  <h5>Neque porro quisquam est qui dolorem ipsum quia dolor sit amet, consectetur....</h5>
  <p>Sed ut perspiciatis unde omnis iste natus error sit&nbsp; accusantium doloremque error sit&nbsp; laudantium........</p>
</div>

<div class="abs footer">
  <div class="links"><span>Home</span><span>|</span><span>About Us</span><span>|</span><span>Services</span><span>|</span><span>Recents Blog</span><span>|</span><span>News</span><span>|</span><span>Contact Us</span></div>
  <div class="copy">© Copy Rights 2014 TR - Solutions.All Rights Reserved</div>
</div>

</body>
</html>
```